I need a logo design for a new company based in Tucson called "Mindtrail Lee Corwin". I am a psychotherapist that specializes in clinical psychology with athletes and performers. The final design should incorporate the psychology symbol as a watermark. The logo should convey movement and fluidity. "Mindtrail" is a bit of a play on words combining psychology (head) with sports (coach). Other design interests include mid-century, Harold Ames Whitby. I will want to use the logo for business cards, letterhead and marketing brochures. I will put together a website at a later date. I am attaching a file with some pertinent information for the business card. Thank you.
Lee Corwin
mindtrailleecorwin@quillpost.net

Thank you all for the submissions so far.  I have submitted an additional file with a draft of a new design idea.  Since "mindtrail" is a bit of a play on words, I would like to see something with the two "H's" look something like quotation marks.  If the psychology logo is to be included at all, it needs to be less prominent.     Thank you all.  Lee                               

Target Market(s)

1) Adolescent and adult athletes and performers who are looking to increase their level of performance (Sport and Performance Psychology)
2) Adult psychotherapy patients (Clinical psychology)

Industry/Entity Type

Marketing

Colors

Designer to choose colors to be used in the design.

Requirements
Must have
• 1) Since "mindtrail" is a bit of a play on words, The "H's" need to be in a font that looks somewhat like quotation marks.

Nice to have
• Logo on one side. All other info on the backside?

```html
<!DOCTYPE html>
<html lang="en">
<head>
<meta charset="utf-8">
<title>Mindtrail Lee Corwin – Business Card</title>
<link href="https://fonts.googleapis.com/css2?family=Saira:wght@400;500;600&display=swap" rel="stylesheet">
<style>
  :root {
    --gold: #dba91f;
    --gold-deep: #c9960f;
    --ink: #3a3a3a;
    --rule: #4a4a4a;
    --card: #f7f7f7;
    --card-shade: #e9e9e9;
    --backdrop: #d9d9d9;
    --white: #ffffff;
  }
  * { margin: 0; padding: 0; box-sizing: border-box; }
  html, body { width: 1200px; height: 903px; overflow: hidden; }
  body {
    background: var(--backdrop);
    font-family: "Saira", Arial, sans-serif;
    color: var(--ink);
    position: relative;
  }
  .card {
    position: absolute;
    left: 250px;
    width: 700px;
    height: 400px;
    background: linear-gradient(135deg, var(--white) 0%, var(--card) 55%, var(--card-shade) 100%);
    box-shadow: 0 6px 18px rgba(0,0,0,0.18);
    overflow: hidden;
  }
  .card--back { top: 40px; }
  .card--front { top: 463px; }

  /* back side */
  .social-band {
    position: absolute;
    left: 0; right: 0;
    top: 180px;
    height: 86px;
    background: linear-gradient(90deg, var(--gold-deep), var(--gold) 60%, #e2b52e);
    display: flex;
    align-items: center;
    justify-content: flex-end;
    padding-right: 34px;
    gap: 14px;
    color: var(--white);
  }
  .social-band__label { font-size: 24px; letter-spacing: 1.5px; font-weight: 400; }
  .social-band__network { font-size: 15px; font-weight: 500; letter-spacing: 0.5px; }

  /* front side */
  .contact { position: absolute; left: 34px; top: 30px; width: 380px; }
  .contact__name { color: var(--gold); font-size: 34px; font-weight: 500; letter-spacing: 1.5px; line-height: 1; }
  .contact__role { font-size: 18px; font-weight: 500; letter-spacing: 1px; margin-top: 6px; margin-left: -6px; }
  .contact__row {
    display: flex;
    align-items: flex-start;
    gap: 16px;
    border-bottom: 2px solid var(--rule);
    padding: 12px 0 8px;
    font-size: 15.5px;
    letter-spacing: 0.8px;
    line-height: 1.45;
  }
  .contact__row:first-of-type { margin-top: 22px; border-top: none; }
  .contact__icon { width: 22px; height: 22px; flex: none; margin-top: 2px; }
  .contact__lines { display: flex; flex-direction: column; }

  .brand {
    position: absolute;
    right: 40px;
    top: 120px;
    width: 250px;
    display: flex;
    flex-direction: column;
    align-items: center;
    gap: 22px;
  }
  .brand__dot { width: 110px; height: 110px; border-radius: 50%; background: var(--gold); }
  .brand__name { font-size: 22px; font-weight: 500; letter-spacing: 1px; color: var(--ink); white-space: nowrap; }
</style>
</head>
<body>

<section class="card card--back" aria-label="Card back">
  <div class="social-band">
    <span class="social-band__label">follow us on here:</span>
    <span class="social-band__network">Wavelet</span>
    <span class="social-band__network">Nookbook</span>
    <span class="social-band__network">Tallyho</span>
    <span class="social-band__network">Reelhall</span>
  </div>
</section>

<section class="card card--front" aria-label="Card front">
  <div class="contact">
    <h1 class="contact__name">OWEN HALE</h1>
    <p class="contact__role">FOUNDER</p>

    <div class="contact__row">
      <svg class="contact__icon" viewBox="0 0 24 24" aria-hidden="true">
        <path d="M6 2h4l1.5 5-2.5 1.5c1 2.5 3 4.5 5.5 5.5L16 11.5l5 1.5v4c0 1-1 2-2 2C10 19 5 14 4 5c0-1 1-3 2-3z" fill="none" stroke="var(--gold)" stroke-width="2" stroke-linejoin="round"/>
      </svg>
      <div class="contact__lines"><span>014 772 3051</span><span>128 560 4417</span></div>
    </div>

    <div class="contact__row">
      <svg class="contact__icon" viewBox="0 0 24 24" aria-hidden="true">
        <path d="M12 2a7 7 0 0 0-7 7c0 5 7 13 7 13s7-8 7-13a7 7 0 0 0-7-7z" fill="var(--gold)"/>
        <circle cx="12" cy="9" r="2.6" fill="var(--white)"/>
      </svg>
      <div class="contact__lines"><span>027.9th floor,Ridge Point Avenue TCS</span></div>
    </div>

    <div class="contact__row">
      <svg class="contact__icon" viewBox="0 0 24 24" aria-hidden="true">
        <rect x="2" y="3" width="20" height="13" rx="1" fill="none" stroke="var(--gold)" stroke-width="2"/>
        <path d="M8 21h8M12 16v5" stroke="var(--gold)" stroke-width="2"/>
      </svg>
      <div class="contact__lines"><span>contact@quillpost.net</span><span>www.mindtrailsite.net</span></div>
    </div>
  </div>

  <div class="brand">
    <div class="brand__dot" aria-hidden="true"></div>
    <p class="brand__name">Mindtrail Lee Corwin</p>
  </div>
</section>

</body>
</html>
```